Communication and Marketing agency needs a new presentation card

We are a group of communication and marketing agencies specialized in companies that are in the logistics and industrial sector. The head agency is TELVANO Grupo and the group consists of 4 agencies: TELVANO Media, TELVANO Digital, TELVANO Research and DifundeEnPantalla. We hace 4 offices in Spain (Madrid, Barcelona, Valencia and Murcia). We are looking for a clean and attractive design that transmits our experience, brand presence in the market and knowledge to those who receive the card.It has to maintain the colors of the logo that is attached.
Target Market(s)
logistics and industrial sector
Marketing department
Contact Information for Business Card
Clean and attractive design

```html
<!DOCTYPE html>
<html lang="en">
<head>
<meta charset="utf-8">
<title>TELVANO Grupo – Business Card</title>
<link href="https://fonts.googleapis.com/css2?family=Roboto:wght@300;400;500;700&display=swap" rel="stylesheet">
<style>
  :root{
    --red:#b31f2a;
    --ink:#3b3b3b;
    --grey:#6e6e6e;
    --rule:#8a8a8a;
    --paper:#ffffff;
    --map:#efefef;
    --stage:#2b2b2b;
  }
  *{box-sizing:border-box;margin:0;padding:0}
  html,body{width:1200px;height:895px;overflow:hidden;background:var(--stage)}
  body{font-family:"Roboto",Arial,sans-serif;position:relative}
  .card{position:absolute;left:290px;width:620px;height:354px;background:var(--paper);overflow:hidden;box-shadow:0 8px 24px rgba(0,0,0,.45)}
  .card--front{top:50px}
  .card--back{top:444px}
  .card__band{position:absolute;left:0;top:0;bottom:0;width:30px;background:var(--red)}

  .brand{position:absolute;text-align:right;color:var(--red);font-weight:300;line-height:1}
  .brand__name{font-size:52px;letter-spacing:3px}
  .brand__sub{font-size:30px;margin-top:2px}

  /* front */
  .front__map{position:absolute;left:200px;top:70px;width:250px;height:200px;background:var(--map);border-radius:40% 55% 45% 50%}
  .front .brand{right:40px;top:34px}
  .offices{position:absolute;right:40px;top:162px;font-size:13px;letter-spacing:2px;color:var(--ink)}
  .front__rule{position:absolute;left:110px;right:40px;top:196px;height:1px;background:var(--rule)}
  .agencies{position:absolute;left:60px;right:40px;bottom:28px;display:flex;justify-content:space-between;align-items:flex-end;border-bottom:1px solid var(--rule);padding-bottom:12px}
  .agency{font-size:17px;font-weight:300;color:var(--ink);letter-spacing:1px}
  .agency--accent{color:var(--red)}

  /* back */
  .back .brand{right:40px;top:36px}
  .back__mark{position:absolute;left:120px;top:90px;width:170px;height:170px;border-radius:50%;background:#f6f0ee}
  .back__rule-red{position:absolute;right:40px;top:178px;width:300px;height:2px;background:var(--red)}
  .address{position:absolute;right:40px;top:192px;text-align:right;font-size:14px;color:var(--ink);line-height:1.4}
  .person{position:absolute;left:60px;top:210px}
  .person__name{font-size:30px;font-weight:700;color:var(--red);line-height:1}
  .person__name span{color:var(--ink)}
  .person__role{font-size:14px;color:var(--ink);margin-top:3px}
  .back__rule{position:absolute;left:60px;right:300px;top:264px;height:1px;background:var(--rule)}
  .contacts{position:absolute;left:60px;top:272px;list-style:none;font-size:14px;color:var(--ink);line-height:1.35}
  .contacts li{display:flex;align-items:center;gap:8px}
  .contacts svg{width:11px;height:11px;fill:var(--red)}
</style>
</head>
<body>

<section class="card card--front front">
  <div class="card__band"></div>
  <div class="front__map" role="img" aria-label="Faint map of Spain marking the four office cities"></div>
  <div class="brand">
    <div class="brand__name">TELVANO</div>
    <div class="brand__sub">Grupo</div>
  </div>
  <p class="offices">Madrid | Barcelona | Valencia | Murcia</p>
  <div class="front__rule"></div>
  <div class="agencies">
    <span class="agency agency--accent">TELVANO Media</span>
    <span class="agency">TELVANO Digital</span>
    <span class="agency">TELVANO Research</span>
    <span class="agency agency--accent">DifundeEnPantalla</span>
  </div>
</section>

<section class="card card--back back">
  <div class="card__band"></div>
  <div class="back__mark"></div>
  <div class="brand">
    <div class="brand__name">TELVANO</div>
    <div class="brand__sub">Grupo</div>
  </div>
  <div class="back__rule-red"></div>
  <p class="address">2450 Calle Ronda Ste. B<br>Alcorcón, MD 28921</p>
  <div class="person">
    <p class="person__name"><span>Adrián</span> Solera</p>
    <p class="person__role">Director</p>
  </div>
  <div class="back__rule"></div>
  <ul class="contacts">
    <li><svg viewBox="0 0 12 12"><rect x="3" y="0" width="6" height="12" rx="1"/></svg>014 220 5318</li>
    <li><svg viewBox="0 0 12 12"><path d="M2 1l3 0 1 3-2 1c1 2 2 3 3 3l1-2 3 1 0 3c-6 1-10-3-9-9z"/></svg>126 447 9021</li>
    <li><svg viewBox="0 0 12 12"><path d="M0 2h12v8H0z M0 2l6 5 6-5" stroke="#fff" stroke-width=".8"/></svg>info@telvanogrupo.com</li>
    <li><svg viewBox="0 0 12 12"><circle cx="6" cy="6" r="6"/></svg>www.telvanogrupo.com</li>
  </ul>
</section>

</body>
</html>
```